Business Card Design

Brambleford Hearth is the name of my health coaching business. My tag line is "where simple food meets daily life." I will be working with clients one-on-one and in groups. My target clients are women "of a certain age" who want to be more comfortable in their own skin. We will work together in a 6-month program. The coaching sessions will take place in my kitchen. I will also be conducting monthly cooking classes and field trips - to farmer's markets, speciality markets etc.. for my clients.
Updates

the business name is Brambleford Hearth - I'm not sure how the p got in there at the end of the name

Thank you

Please include the website - www.bramblefordhearth-example.com and the tag line:

where simple food meets daily life on the business card.

Thank you

Please add the phone number to the business card - sorry, I forgot to state that in the original brief

(555) 217-4860

Target Market(s)

Women "of a certain age" who want to be more comfortable in their own skin

Industry/Entity Type

Cooking

Contact Information for Business Card

Brambleford Hearth
where simple food meets daily life

Tessa Marlowe
Health Coach
(555) 217-4860

Font styles to use
Serif
Sans Serif

Requirements
Must have
• front & back design
I typical like soft colors - and have tended toward greens over time - I'm open although I would not like bright reds, yellows etc..

```html
<!DOCTYPE html>
<html lang="en">
<head>
<meta charset="utf-8">
<title>Brambleford Hearth — Business Card</title>
<link rel="stylesheet" href="https://fonts.googleapis.com/css2?family=PT+Sans:ital,wght@0,400;0,700;1,400&family=PT+Sans+Narrow:wght@400;700&display=swap">
<style>
  :root {
    --page-bg: #e4e4e2;
    --card-green: #4c8a37;
    --ink-light: #cfeabd;
    --tag-box: #d4efc2;
    --ink-dark: #2e6322;
    --rule: #d9f0ca;
  }
  * { margin: 0; padding: 0; box-sizing: border-box; }
  html, body { width: 1200px; height: 900px; overflow: hidden; background: var(--page-bg); }
  .canvas { position: relative; width: 1200px; height: 900px; }
  .card {
    position: absolute; left: 75px; top: 150px; width: 1050px; height: 600px;
    background: var(--card-green); overflow: hidden;
    box-shadow: 0 10px 30px rgba(0,0,0,0.25);
    font-family: "PT Sans", sans-serif; color: var(--ink-light);
  }
  .card__pattern { position: absolute; inset: 0; width: 100%; height: 100%; }
  .brand {
    position: absolute; left: 160px; top: 150px; display: flex; align-items: flex-start;
    font-weight: 700; line-height: 1; color: var(--ink-light); white-space: nowrap;
  }
  .brand__first { font-size: 86px; letter-spacing: -1px; }
  .brand__second { font-size: 60px; margin-left: 14px; margin-top: 44px; }
  .tagline {
    position: absolute; left: 560px; top: 262px; white-space: nowrap;
    font-family: "PT Sans Narrow", sans-serif; font-style: italic; font-size: 30px;
    letter-spacing: 1px; color: var(--ink-light);
  }
  .person { position: absolute; right: 60px; top: 58px; text-align: right; }
  .person__name { display: inline-block; background: var(--tag-box); color: var(--ink-dark); font-weight: 700; font-size: 36px; padding: 2px 18px 4px; }
  .person__role { font-weight: 700; font-size: 36px; color: var(--ink-light); margin-top: 2px; padding-right: 18px; }
  .contact { position: absolute; border-bottom: 3px solid var(--rule); font-family: "PT Sans Narrow", sans-serif; font-size: 25px; padding: 0 6px 6px; display: flex; justify-content: space-between; align-items: flex-end; white-space: nowrap; }
  .contact--email { left: 30px; top: 372px; width: 400px; }
  .contact--web { left: 280px; top: 448px; width: 390px; }
  .contact--phone { left: 560px; top: 520px; width: 440px; font-family: "PT Sans", sans-serif; font-weight: 700; font-size: 34px; letter-spacing: 2px; }
  .contact__icon { width: 34px; height: 34px; flex: none; margin-bottom: 2px; }
</style>
</head>
<body>
<main class="canvas">
  <section class="card" aria-label="Business card front">
    <svg class="card__pattern" viewBox="0 0 1050 600" role="img" aria-label="Faint pattern of kitchen utensils, cups and bowls">
      <defs>
        <linearGradient id="patternTone" x1="0" y1="0" x2="1" y2="1">
          <stop offset="0" stop-color="#4f8d3a"/>
          <stop offset="0.5" stop-color="#57953f"/>
          <stop offset="1" stop-color="#4a8735"/>
        </linearGradient>
      </defs>
      <rect width="1050" height="600" fill="url(#patternTone)"/>
    </svg>

    <h1 class="brand"><span class="brand__first">Brambleford</span><span class="brand__second">Hearth</span></h1>
    <p class="tagline">where simple food meets daily life</p>

    <div class="person">
      <div class="person__name">Tessa Marlowe</div>
      <div class="person__role">Health Coach</div>
    </div>

    <div class="contact contact--email">
      <span>tessa@bramblefordhearth-example.com</span>
      <svg class="contact__icon" viewBox="0 0 34 34" aria-hidden="true">
        <rect x="4" y="10" width="26" height="18" fill="none" stroke="#d9f0ca" stroke-width="2.5"/>
        <path d="M4 10 L17 20 L30 10" fill="none" stroke="#d9f0ca" stroke-width="2.5"/>
      </svg>
    </div>

    <div class="contact contact--web">
      <span>www.bramblefordhearth-example.com</span>
      <svg class="contact__icon" viewBox="0 0 34 34" aria-hidden="true">
        <circle cx="17" cy="17" r="13" fill="none" stroke="#d9f0ca" stroke-width="2.5"/>
        <ellipse cx="17" cy="17" rx="6" ry="13" fill="none" stroke="#d9f0ca" stroke-width="2"/>
        <path d="M4 17 H30 M6 10 H28 M6 24 H28" stroke="#d9f0ca" stroke-width="2"/>
      </svg>
    </div>

    <div class="contact contact--phone">
      <span>(555) 217-4860</span>
      <svg class="contact__icon" viewBox="0 0 34 34" aria-hidden="true">
        <rect x="10" y="3" width="15" height="28" rx="2.5" fill="none" stroke="#d9f0ca" stroke-width="2.5"/>
        <line x1="14" y1="26" x2="21" y2="26" stroke="#d9f0ca" stroke-width="2"/>
      </svg>
    </div>
  </section>
</main>
</body>
</html>
```